Brivolt Technologies business card design

We need a business card designed with our new logo. it would be great if the card could communicate it is a technology based company.

Target Market(s)

system integrators

Industry/Entity Type

technology, IOT

Contact Information for Business Card

Name, designation, Address, telephone number, email address

Requirements
Must have
• logo and company name
Nice to have
• something to do with technology

```html
<!DOCTYPE html>
<html lang="en">
<head>
<meta charset="utf-8">
<title>Brivolt Technologies Business Card</title>
<link rel="stylesheet" href="https://fonts.googleapis.com/css2?family=Inter:wght@400;500;600;700&display=swap">
<style>
  :root {
    --stage: #e6e6e6;
    --paper: #ffffff;
    --charcoal: #3d3d3d;
    --ink: #3a3a3a;
    --orange: #f7931e;
    --white: #ffffff;
  }
  * { margin: 0; padding: 0; box-sizing: border-box; }
  html, body {
    width: 1135px;
    height: 1200px;
    overflow: hidden;
    background: var(--stage);
    font-family: "Inter", Arial, sans-serif;
  }
  .card {
    position: absolute;
    left: 205px;
    width: 726px;
    height: 415px;
    box-shadow: 0 6px 18px rgba(0,0,0,0.18);
  }
  .card--front { top: 145px; background: var(--paper); }
  .card--back  { top: 641px; background: var(--charcoal); }

  .wordmark {
    position: absolute;
    display: flex;
    align-items: center;
    gap: 12px;
  }
  .wordmark__square {
    width: 22px;
    height: 22px;
    background: var(--orange);
  }
  .wordmark__text {
    font-weight: 700;
    line-height: 1;
    letter-spacing: 0.5px;
  }
  .card--front .wordmark { left: 59px; top: 70px; }
  .card--front .wordmark__text { font-size: 30px; color: var(--charcoal); }
  .card--back .wordmark { left: 50%; top: 50%; transform: translate(-50%, -50%); gap: 16px; }
  .card--back .wordmark__square { width: 30px; height: 30px; }
  .card--back .wordmark__text { font-size: 42px; color: var(--white); }

  .contact {
    position: absolute;
    left: 413px;
    top: 180px;
    color: var(--ink);
  }
  .contact__name {
    font-size: 26px;
    font-weight: 600;
    color: var(--orange);
    line-height: 1.1;
  }
  .contact__role {
    font-size: 17px;
    font-weight: 400;
    margin-top: 4px;
    letter-spacing: 0.3px;
  }
  .contact__address {
    font-size: 18px;
    line-height: 24px;
    margin-top: 10px;
    font-style: normal;
  }
  .contact__list {
    list-style: none;
    margin-top: 8px;
    font-size: 18px;
    line-height: 24px;
  }
  .contact__list li {
    display: flex;
    align-items: center;
    gap: 6px;
  }
  .contact__list svg {
    width: 14px;
    height: 14px;
    flex: none;
    margin-left: -1px;
  }
</style>
</head>
<body>
  <section class="card card--front">
    <div class="wordmark">
      <span class="wordmark__square"></span>
      <span class="wordmark__text">Brivolt Technologies</span>
    </div>

    <div class="contact">
      <p class="contact__name">DANIEL ROURKE</p>
      <p class="contact__role">DIRECTOR</p>
      <address class="contact__address">1470 Alder Lane<br>Fairview, OR 97024</address>
      <ul class="contact__list">
        <li>
          <svg viewBox="0 0 16 16" aria-hidden="true"><path d="M4 1.5 6 4 4.8 5.6c.8 2 2.4 3.8 4.6 4.8L11 9l2.6 2-1.4 2.6C7 13 2.6 8 2.5 2.8Z" fill="none" stroke="#f7931e" stroke-width="1.5" stroke-linejoin="round"/></svg>
          <span>(555) 014-2287</span>
        </li>
        <li>
          <svg viewBox="0 0 16 16" aria-hidden="true"><rect x="1.5" y="3.5" width="13" height="9" fill="none" stroke="#f7931e" stroke-width="1.5"/><path d="M1.5 3.5 8 9l6.5-5.5" fill="none" stroke="#f7931e" stroke-width="1.5"/></svg>
          <span>hello@brivolttech.com</span>
        </li>
        <li>
          <svg viewBox="0 0 16 16" aria-hidden="true"><circle cx="8" cy="8" r="6.5" fill="none" stroke="#f7931e" stroke-width="1.3"/><ellipse cx="8" cy="8" rx="2.8" ry="6.5" fill="none" stroke="#f7931e" stroke-width="1.1"/><path d="M1.5 8h13M2.5 5h11M2.5 11h11" stroke="#f7931e" stroke-width="1"/></svg>
          <span>brivolttech.com</span>
        </li>
      </ul>
    </div>
  </section>

  <section class="card card--back">
    <div class="wordmark">
      <span class="wordmark__square"></span>
      <span class="wordmark__text">Brivolt Technologies</span>
    </div>
  </section>
</body>
</html>
```